Business Card and Letterhead for Pimlu - modern real estate business

I need a double sided business card design for Pimlu. Please see business card brief here https://files.trelvonadocs.com/sheet/r/7QzTmWbaXLJnoPEd-kRyUgFhHsstbvCe2qfoMxDa_pz/view?mode=shared

Please feel free to design the business cards however you feel best. I am happy to give some creative freedoms and then provide feedback from there.

Please then also create a letterhead to match the business card design

Colors

Designer to choose colors to be used in the design.

Requirements
Must have
• Must be a modern, elegant business card which looks very professional

```html
<!DOCTYPE html>
<html lang="en">
<head>
<meta charset="utf-8">
<title>Pimlu Business Card</title>
<link rel="stylesheet" href="https://fonts.googleapis.com/css2?family=Exo+2:wght@400;600;700&display=swap">
<style>
  :root {
    --page-bg: #e6e6e8;
    --card-black: #1b1b1e;
    --card-white: #ffffff;
    --brand-red: #e3141f;
    --ink-dark: #1e1e1e;
    --ink-grey: #555555;
    --photo-top: #d9dadd;
    --photo-bottom: #4a4d55;
  }
  * { box-sizing: border-box; margin: 0; padding: 0; }
  html, body {
    width: 1200px; height: 960px; overflow: hidden;
    background: var(--page-bg);
    font-family: "Exo 2", "Segoe UI", sans-serif;
  }
  .canvas { position: relative; width: 1200px; height: 960px; }
  .card {
    position: absolute; left: 250px; width: 700px; height: 400px;
    overflow: hidden;
    box-shadow: 0 10px 30px rgba(0,0,0,0.18);
  }
  .card-back { top: 60px; background: var(--card-black); display: flex; align-items: center; justify-content: center; }
  .brand-name {
    color: var(--brand-red); font-weight: 600; font-size: 110px;
    letter-spacing: 10px; text-transform: uppercase; line-height: 1;
  }
  .card-front { top: 500px; background: var(--card-white); }
  .portrait-area {
    position: absolute; right: 0; top: 0; width: 330px; height: 400px;
    background: linear-gradient(180deg, var(--photo-top) 0%, var(--photo-top) 30%, var(--photo-bottom) 100%);
  }
  .accent-bar {
    position: absolute; left: 0; top: 246px; width: 14px; height: 40px;
    background: var(--brand-red);
  }
  .agent-block { position: absolute; left: 56px; top: 236px; }
  .agent-name { color: var(--brand-red); font-weight: 700; font-size: 28px; line-height: 1.1; }
  .agent-title { color: var(--ink-dark); font-weight: 600; font-size: 16px; margin-top: 4px; }
  .contact-list { list-style: none; position: absolute; left: 76px; top: 306px; }
  .contact-item {
    display: flex; align-items: center; gap: 12px;
    color: var(--ink-grey); font-size: 15px; line-height: 22px;
  }
  .contact-item svg { width: 14px; height: 14px; flex: none; fill: var(--brand-red); }
</style>
</head>
<body>
<main class="canvas">
  <section class="card card-back" aria-label="Card back">
    <span class="brand-name">Pimlu</span>
  </section>

  <section class="card card-front" aria-label="Card front">
    <div class="portrait-area" role="img" aria-label="Portrait photo of the agent in a dark blazer"></div>
    <div class="accent-bar"></div>
    <div class="agent-block">
      <h1 class="agent-name">Rowan Pell</h1>
      <p class="agent-title">Licenced Real Estate Agent</p>
    </div>
    <ul class="contact-list">
      <li class="contact-item">
        <svg viewBox="0 0 24 24" aria-hidden="true"><path d="M6.6 10.8a15 15 0 0 0 6.6 6.6l2.2-2.2c.3-.3.7-.4 1-.2 1.1.4 2.3.6 3.6.6.6 0 1 .4 1 1V20c0 .6-.4 1-1 1A17 17 0 0 1 3 4c0-.6.4-1 1-1h3.5c.6 0 1 .4 1 1 0 1.3.2 2.5.6 3.6.1.3 0 .7-.2 1z"/></svg>
        0400 318 274
      </li>
      <li class="contact-item">
        <svg viewBox="0 0 24 24" aria-hidden="true"><path d="M2 5h20v14H2zm2 2v.5l8 5 8-5V7l-8 5z"/></svg>
        rowan@pimlu.com
      </li>
      <li class="contact-item">
        <svg viewBox="0 0 24 24" aria-hidden="true"><circle cx="12" cy="12" r="10"/></svg>
        www.pimlu.com
      </li>
      <li class="contact-item">
        <svg viewBox="0 0 24 24" aria-hidden="true"><path d="M12 2a7 7 0 0 0-7 7c0 5 7 13 7 13s7-8 7-13a7 7 0 0 0-7-7zm0 9.5A2.5 2.5 0 1 1 12 6.5a2.5 2.5 0 0 1 0 5z"/></svg>
        PO Box 1190, Larkfield NSW 2790
      </li>
    </ul>
  </section>
</main>
</body>
</html>
```